Teeth Whitening Clinic Website Redesign - Social Proof Theme

NEW TEETH SITEREVAMP CURRENT WEBSITE:WWW.SANDIEGOSTEETHWHITENING.COMTHEME:SOCIAL PROOF/5 STAR REVIEWS/TESTIMONIALS THEME:https://maps.example.net/QxRvPLoKzN84 I want a testimonial themed, social proof themed website so customers will be sold by testimonials all over the website….I like a nice clean simple site but with all important factors standing out like CALLS TO ACTIONS, for example the $99 special link in header on original design. Also, testimonials throughout the website placed methodically as not to be FORCED and CLUTTEREDKeep all same exact content for all pages and elements of current design. All buttons, calls to action, navigation, etc. Please do not leave anything out from current design. SPECIAL INSTRUCTIONS for banner image:I want to use actual customer photos inside the banner image in a way that really pops and grabs attention. Please grab some customer photos from my PG Account, fk or rateway account: Also, I want to integrate 5 star rateway logo, friendbook review 5 stars icon, searchly business page 5 stars icon, etc. on the banner as well to show social proof as much as possible. Actual customer photos to be used throughout website:https://www.photogram.example/brightharborsmilestudioplace/ https://www.friendbook.com/SDTeethWhitening/https://www.reviewhub.example/biz/bright-harbor-smile-studio-place-bright-harbor-5 Reviews:https://www.reviewhub.example/biz/bright-harbor-smile-studio-place-bright-harbor-5 https://www.friendbook.com/pg/SDTeethWhitening/reviews/?ref=page_internalhttps://goo.gl/maps/TmJcABLAJwC2 Please do home page first to come up with theme then after approval home page we can move forward additional pages.

Target Market(s)

PEOPLE THAT CARE ABOUT DENTAL HYGEINE AND OR CARE ABOUT THEIR TEETH SMILE

Industry/Entity Type

Dental Clinic

Number of Pages Required

5+ page

Colors

Designer to choose colors to be used in the design.

Requirements
Must have
• NEW TEETH SITE
• REVAMP CURRENT WEBSITE:
• WWW.BRIGHTHARBORSMILESTUDIO.EXAMPLE
• THEME:
• SOCIAL PROOF/5 STAR REVIEWS/TESTIMONIALS THEME:
• https://maps.example.net/QxRvPLoKzN84
• I want a testimonial themed, social proof themed website so customers will be sold by testimonials all over the website….I like a nice clean simple site but with all important factors standing out like CALLS TO ACTIONS, for example the $99 special link in header on original design. Also, testimonials throughout the website placed methodically as not to be FORCED and CLUTTERED
• Keep all same exact content for all pages and elements of current design. All buttons, calls to action, navigation, etc. Please do not leave anything out from current design.
• SPECIAL INSTRUCTIONS for banner image:
• I want to use actual customer photos inside the banner image in a way that really pops and grabs attention. Please grab some customer photos from my PG Account, fk or rateway account:
• Also, I want to integrate 5 star rateway logo, friendbook review 5 stars icon, searchly business page 5 stars icon, etc. on the banner as well to show social proof as much as possible.
• Actual customer photos to be used throughout website:
• https://www.photogram.example/brightharborsmilestudioplace/
• https://www.friendbook.example/BHSmileStudio/
• https://www.reviewhub.example/biz/bright-harbor-smile-studio-place-bright-harbor-5
• Reviews:
• https://www.friendbook.example/pg/BHSmileStudio/reviews/?ref=page_internal
• Please do home page first to come up with theme then after approval home page we can move forward additional pages.
Nice to have
• NEW TEETH SITE
• REVAMP CURRENT WEBSITE:
• THEME:
• Reviews:
Should not have
• NEW TEETH SITE
• REVAMP CURRENT WEBSITE:
• THEME:
• Reviews:

```html
<!DOCTYPE html>
<html lang="en">
<head>
<meta charset="utf-8">
<title>Bright Harbor Smile Studio</title>
<link href="https://fonts.googleapis.com/css2?family=Cinzel:wght@400;600&family=Open+Sans:ital,wght@0,400;0,600;0,700;1,400&display=swap" rel="stylesheet">
<style>
:root{
  --teal:#1fb1c8;
  --teal-dark:#1597ad;
  --ink:#2b2b2b;
  --muted:#6e6e6e;
  --light:#f4f4f4;
  --line:#dcdcdc;
  --star:#f5d33a;
  --dark:#1a1a1a;
  --head-grey:#5b5b5b;
}
*{box-sizing:border-box;margin:0;padding:0}
html,body{width:1200px;height:4300px;overflow:hidden}
body{position:relative;background:#fff;font-family:"Open Sans",Arial,sans-serif;color:var(--ink)}
.abs{position:absolute}
.serif{font-family:"Cinzel",Georgia,serif;font-weight:400}

/* header */
.brand{left:112px;top:25px;display:flex;align-items:center;gap:10px}
.brand-dot{width:56px;height:56px;border-radius:50%;background:#e9eef1;border:2px solid #cfd8dc}
.brand-name{font-family:"Cinzel",Georgia,serif;font-size:19px;line-height:1.1;color:#6a6a6a}
.brand-name small{display:block;font-family:inherit;font-size:12px;color:var(--teal)}
.info{display:flex;align-items:center;gap:14px;top:34px;font-size:13.5px;line-height:1.6;color:#444}
.info-ico{width:40px;height:40px;border-radius:50%;border:1.5px solid #cfe9ee;display:flex;align-items:center;justify-content:center;color:var(--teal);font-weight:700;font-size:19px}
.nav{left:0;top:108px;width:1200px;height:45px;border-top:1px solid var(--line);display:flex;align-items:center;padding-left:113px;gap:43px;font-size:15px;color:#555}
.nav .active{color:var(--teal)}

/* hero */
.hero{left:0;top:153px;width:1200px;height:558px;background:linear-gradient(90deg,#1aa9c1,#23bdd2)}
.hero-title{left:112px;top:78px;color:#fff;font-size:44px;line-height:58px;letter-spacing:1px}
.btn-ghost{height:62px;border:2px solid #fff;border-radius:31px;color:#fff;font-weight:700;font-size:17px;display:flex;align-items:center;justify-content:center}
.rating{top:392px;color:#fff;text-align:center}
.rating-name{font-size:26px;font-weight:700;display:flex;align-items:center;gap:8px}
.rating-name i{display:inline-block;width:26px;height:26px;border:2px solid #fff;border-radius:4px}
.rating .stars{color:var(--star);font-size:20px;letter-spacing:2px}
.bubble{border-radius:50%;border:5px solid #fff;background:radial-gradient(circle at 45% 40%,#a98b7c,#5a4a5a 60%,#e8e8ea 100%)}

/* about */
.h2{width:1200px;text-align:center;font-family:"Cinzel",Georgia,serif;font-size:40px;color:var(--ink)}
.lead{left:150px;width:900px;text-align:center;font-size:13.5px;line-height:26px;color:#555}
.video{left:396px;top:1001px;width:407px;height:279px;border:1px solid var(--line);box-shadow:0 0 6px rgba(0,0,0,.12);background:#fff}
.video-title{position:absolute;left:30px;top:16px;color:var(--teal);font-size:21px}
.video-panel{position:absolute;left:6px;top:66px;width:148px;height:170px;background:#1ea4d6;color:#fff;font-size:9.5px;line-height:13px;padding:26px 6px 0 4px}
.video-shot{position:absolute;left:154px;top:66px;width:246px;height:170px;background:linear-gradient(90deg,#3d3d3d,#7c7c7c 55%,#2b2b2b)}
.play{position:absolute;left:21px;top:45px;width:58px;height:58px;border-radius:50%;background:#111}
.video-foot{position:absolute;left:6px;top:243px;font-family:"Cinzel",serif;font-size:12px;color:#777}
.btn-outline{height:52px;border:2px solid var(--teal);border-radius:26px;color:var(--teal);font-weight:700;font-size:15px;display:flex;align-items:center;justify-content:center;background:#fff}

/* why */
.why{left:0;top:1485px;width:1200px;height:738px;background:var(--light)}
.feature{width:300px}
.feature-ico{width:76px;height:76px;border-radius:50%;border:2px solid var(--teal);display:flex;align-items:center;justify-content:center}
.feature h3{margin-top:22px;font-size:23px;font-weight:600;color:#222}
.feature p{margin-top:14px;font-size:13.5px;line-height:25px;color:#777}

/* how */
.how{left:112px;top:2330px;width:586px;height:454px;border:1px solid #cfcfcf;background:#fff}
.how h2{position:absolute;left:43px;top:50px;font-family:"Cinzel",serif;font-weight:400;font-size:40px}
.how p{position:absolute;left:43px;top:128px;width:460px;font-size:13.5px;line-height:26px;color:#666}
.how-photo{left:641px;top:2370px;width:452px;height:375px;border:5px solid #fff;box-shadow:0 0 8px rgba(0,0,0,.15);background:linear-gradient(120deg,#e6e3e8,#8a7a8a 45%,#3b3042 75%,#d8d4dc)}

/* testimonials */
.testi{left:0;top:2901px;width:1200px;height:400px;background:linear-gradient(90deg,#9a9ea3,#c2c5c9 50%,#8d9297)}
.testi-title{top:95px;width:1200px;text-align:center;font-family:"Cinzel",serif;font-size:40px;color:#fff}
.card{width:320px;top:170px;color:#fff}
.avatar{position:absolute;left:0;top:0;width:72px;height:72px;border-radius:50%;border:3px solid #fff;background:linear-gradient(135deg,#c9b49a,#6b7c8a)}
.quote{position:absolute;left:84px;top:0;width:236px;font-style:italic;font-size:12.5px;line-height:23px}
.quote b{font-size:20px;font-style:normal;margin-right:8px}
.who{position:absolute;left:84px;top:96px;font-weight:700;font-size:13px}
.card .stars{position:absolute;left:84px;top:116px;color:var(--star);font-size:20px;letter-spacing:4px}
.arrow{width:36px;height:36px;border-radius:50%;border:1.5px solid #fff;top:229px;display:flex;align-items:center;justify-content:center}

/* compare */
.table{left:108px;top:3502px;width:980px;height:334px;display:flex;gap:5px}
.col{flex:1;background:#fff;box-shadow:0 1px 5px rgba(0,0,0,.18)}
.col-head{height:53px;background:var(--head-grey);color:#fff;font-weight:700;font-size:17px;display:flex;align-items:center;justify-content:center;letter-spacing:.5px}
.col-head.brandhead{background:var(--teal);font-family:"Cinzel",serif;font-weight:600;font-size:14px;letter-spacing:0;gap:6px}
.col-head.brandhead i{width:22px;height:22px;border-radius:50%;background:#fff}
.col ul{list-style:none;padding-top:26px}
.col li{height:47px;text-align:center;font-size:13.5px;color:#777}
.col.labels li{color:#222;font-weight:600;font-size:14px}

/* footer */
.footer{left:0;top:3946px;width:1200px;height:354px;background:var(--dark);color:#fff}
.socials{left:486px;top:80px;display:flex;gap:10px}
.socials span{width:50px;height:50px;border-radius:50%;border:1.5px solid #fff;display:flex;align-items:center;justify-content:center;font-size:14px;font-weight:600}
.foot-line{width:1200px;text-align:center;font-size:14px}
.foot-links{font-size:13.5px;line-height:27px}
</style>
</head>
<body>

<!-- header -->
<div class="abs brand"><span class="brand-dot"></span><div class="brand-name">Bright Harbor<small>Smile Studio</small></div></div>
<div class="abs info" style="left:380px;top:34px"><span class="info-ico">$</span><div>Click Here to Get Our $99 Teeth<br>Whitening Deal (Reg: $378)</div></div>
<div class="abs info" style="left:667px;top:34px"><span class="info-ico"><svg width="16" height="20" viewBox="0 0 16 20"><path d="M8 1a6 6 0 0 1 6 6c0 5-6 12-6 12S2 12 2 7a6 6 0 0 1 6-6z" fill="none" stroke="currentColor" stroke-width="2"/><circle cx="8" cy="7" r="2" fill="currentColor"/></svg></span><div>4410 Harborview Ave. #118<br>Bright Harbor, CA 90210</div></div>
<div class="abs info" style="left:935px;top:34px"><span class="info-ico"><svg width="18" height="18" viewBox="0 0 24 24"><path d="M6.6 10.8a15 15 0 0 0 6.6 6.6l2.2-2.2c.3-.3.7-.4 1-.2 1.1.4 2.3.6 3.6.6.6 0 1 .4 1 1V20c0 .6-.4 1-1 1A17 17 0 0 1 3 4c0-.6.4-1 1-1h3.5c.6 0 1 .4 1 1 0 1.3.2 2.5.6 3.6.1.3 0 .7-.2 1z" fill="currentColor"/></svg></span><div>Call us on<br>1-555-014-2290</div></div>

<nav class="abs nav"><span class="active">Home</span><span>Our Process</span><span>Photos</span><span>Free Treatments</span><span>Testimonials</span><span>Blog</span><span>FAQ</span><span>Contact</span><span>Gift Certificates</span></nav>

<!-- hero -->
<section class="abs hero">
  <h1 class="abs hero-title serif">Get That White<br>Smile You've Always<br>Wanted</h1>
  <div class="abs btn-ghost" style="left:112px;top:277px;width:208px">BOOK ONLINE</div>
  <div class="abs btn-ghost" style="left:334px;top:277px;width:208px">CONTACT US</div>
  <div class="abs rating" style="left:112px"><div class="rating-name">rateway</div><div class="stars">★★★★★</div></div>
  <div class="abs rating" style="left:267px"><div class="rating-name"><i></i>friendbook</div><div class="stars">★★★★★</div></div>
  <div class="abs rating" style="left:442px"><div class="rating-name">searchly<i></i></div><div class="stars">★★★★★</div></div>
</section>
<div class="abs bubble" style="left:663px;top:157px;width:110px;height:110px" role="img" aria-label="Happy customers posing with staff"></div>
<div class="abs bubble" style="left:576px;top:253px;width:144px;height:144px" role="img" aria-label="Customer holding a smile sign"></div>
<div class="abs bubble" style="left:733px;top:212px;width:220px;height:220px" role="img" aria-label="Customer and team holding smile with cheer sign"></div>
<div class="abs bubble" style="left:993px;top:156px;width:166px;height:166px" role="img" aria-label="Team with a first whitening sign"></div>
<div class="abs bubble" style="left:609px;top:399px;width:184px;height:184px" role="img" aria-label="Customer holding new smile sign"></div>
<div class="abs bubble" style="left:785px;top:468px;width:226px;height:226px" role="img" aria-label="Customer holding best cash spent sign"></div>
<div class="abs bubble" style="left:985px;top:337px;width:214px;height:214px" role="img" aria-label="Customer group with whitening team"></div>
<div class="abs bubble" style="left:1019px;top:561px;width:146px;height:146px" role="img" aria-label="Team photo with happy customer"></div>

<!-- about -->
<h2 class="abs h2" style="top:818px">Bright Harbor Smile Studio</h2>
<p class="abs lead" style="top:888px">Bright Harbor Smile Studio features state-of-the-art technologies that are safe, industry-unique and very cost-effective. Our teeth whitening system utilizes the latest blue light whitening technology. Our Blue Light Systems are calibrated precisely for optimal activation of our exclusive hydrogen peroxide based whitening solution which is manufactured in a FDA registered facility in the USA.</p>
<div class="abs video">
  <div class="video-title">Bright Harbor Smile Studio</div>
  <div class="video-panel">When you walk in the door, you will be greeted by our very friendly staff. We take pride in providing outstanding customer service.<br><br>We will send you a text message with a link to our online consent form that you will sign directly from your smart phone.</div>
  <div class="video-shot" role="img" aria-label="Video still of a patient arriving at the studio"><div class="play"><svg width="58" height="58"><path d="M23 18l18 11-18 11z" fill="#fff"/></svg></div></div>
  <div class="video-foot">Bright Harbor</div>
</div>
<div class="abs btn-outline" style="left:519px;top:1325px;width:160px">READ MORE</div>

<!-- why -->
<section class="abs why">
  <h2 class="abs h2" style="top:88px">Why Choose Us</h2>
  <div class="abs feature" style="left:112px;top:173px"><div class="feature-ico"><svg width="34" height="24" viewBox="0 0 34 24"><rect x="1" y="3" width="32" height="18" rx="2" fill="none" stroke="#1fb1c8" stroke-width="2.5"/><circle cx="17" cy="12" r="5" fill="#1fb1c8"/></svg></div><h3>PRICE</h3><p>Nam libero tempore, cum soluta nobis estelig endi optio cumque nihil impedit quo minus id quod maxime placeat face.</p></div>
  <div class="abs feature" style="left:454px;top:173px"><div class="feature-ico"><svg width="30" height="28" viewBox="0 0 30 28"><rect x="1" y="1" width="28" height="26" fill="none" stroke="#1fb1c8" stroke-width="2.5"/><rect x="7" y="13" width="3" height="10" fill="#1fb1c8"/><rect x="12" y="8" width="3" height="15" fill="#1fb1c8"/><rect x="17" y="11" width="3" height="12" fill="#1fb1c8"/><rect x="22" y="6" width="3" height="17" fill="#1fb1c8"/></svg></div><h3>RESULTS</h3><p>Nam libero tempore, cum soluta nobis estelig endi optio cumque nihil impedit quo minus id quod maxime placeat face.</p></div>
  <div class="abs feature" style="left:798px;top:173px"><div class="feature-ico"><svg width="30" height="30" viewBox="0 0 30 30"><circle cx="15" cy="15" r="11" fill="none" stroke="#1fb1c8" stroke-width="3.5"/><path d="M22 8L8 22" stroke="#1fb1c8" stroke-width="3.5"/></svg></div><h3>NO PAIN</h3><p>Nam libero tempore, cum soluta nobis estelig endi optio cumque nihil impedit quo minus id quod maxime placeat face.</p></div>
  <div class="abs feature" style="left:112px;top:425px"><div class="feature-ico"><svg width="34" height="30" viewBox="0 0 34 30"><circle cx="13" cy="17" r="8" fill="none" stroke="#1fb1c8" stroke-width="5" stroke-dasharray="4 2.3"/><circle cx="13" cy="17" r="3" fill="#1fb1c8"/><circle cx="26" cy="8" r="5" fill="none" stroke="#1fb1c8" stroke-width="3.5" stroke-dasharray="3 1.8"/></svg></div><h3>SERVICE</h3><p>Nam libero tempore, cum soluta nobis estelig endi optio cumque nihil impedit quo minus id quod maxime placeat face.</p></div>
  <div class="abs feature" style="left:454px;top:425px"><div class="feature-ico"><svg width="32" height="28" viewBox="0 0 32 28"><ellipse cx="15" cy="12" rx="12" ry="9" fill="none" stroke="#1fb1c8" stroke-width="2.5"/><path d="M8 19l-3 6 8-4" fill="#1fb1c8"/><path d="M10 11h10M10 15h7" stroke="#1fb1c8" stroke-width="2"/></svg></div><h3>CONVENIENCE</h3><p>Nam libero tempore, cum soluta nobis estelig endi optio cumque nihil impedit quo minus id quod maxime placeat face.</p></div>
  <div class="abs feature" style="left:798px;top:425px"><div class="feature-ico"><svg width="28" height="28" viewBox="0 0 28 28"><rect x="2" y="4" width="24" height="22" fill="none" stroke="#1fb1c8" stroke-width="2.5"/><rect x="2" y="4" width="24" height="6" fill="#1fb1c8"/><path d="M8 1v6M20 1v6" stroke="#1fb1c8" stroke-width="2.5"/><path d="M6 14h16M6 18h16M6 22h16M10 11v13M14 11v13M18 11v13" stroke="#1fb1c8" stroke-width="1.3"/></svg></div><h3>ONLINE BOOKING</h3><p>Nam libero tempore, cum soluta nobis estelig endi optio cumque nihil impedit quo minus id quod maxime placeat face.</p></div>
</section>

<!-- how it works -->
<section class="abs how">
  <h2>How It Works</h2>
  <p>We have a very effective teeth whitening treatment that is guaranteed to get you quick results in about 1 hour. To start the treatment you'll apply a Hydrogen Peroxide based whitening agent to your teeth. We then place our cold blue light directly in front of your exposed teeth for 15 minutes per treatment. The lighting systems we use activate the whitening agent and thats what accelerates the whitening process, giving you whiter teeth in less than an hour.</p>
  <div class="abs btn-outline" style="left:43px;top:344px;width:160px">READ MORE</div>
</section>
<div class="abs how-photo" role="img" aria-label="Happy customer with the team holding best patient ever sign"></div>

<!-- testimonials -->
<section class="abs testi" role="region" aria-label="Testimonials">
  <h2 class="abs testi-title">Testimonials</h2>
  <div class="abs arrow" style="left:29px"><svg width="12" height="14"><path d="M9 2L3 7l6 5" fill="none" stroke="#fff" stroke-width="1.5"/></svg></div>
  <div class="abs arrow" style="left:1134px"><svg width="12" height="14"><path d="M3 2l6 5-6 5" fill="none" stroke="#fff" stroke-width="1.5"/></svg></div>
  <div class="abs card" style="left:112px"><div class="avatar" role="img" aria-label="Reviewer portrait"></div><div class="quote"><b>“</b>"The staff is really friendly and welcoming and Carla did such a good job with my smile!"</div><div class="who">DAN OKORO</div><div class="stars">★★★★☆</div></div>
  <div class="abs card" style="left:447px"><div class="avatar" role="img" aria-label="Reviewer portrait"></div><div class="quote"><b>“</b>"Seriously, Tessa worked her magic hands on my teeth as I played the part of the magician assistant."</div><div class="who">LEE RAVENSWORTH</div><div class="stars">★★★★½</div></div>
  <div class="abs card" style="left:784px"><div class="avatar" role="img" aria-label="Reviewer portrait"></div><div class="quote"><b>“</b>"I also appreciated that they took the Alvarez explain all the instructions and didn't mind me asking addition..</div><div class="who">MIRA TANAKA-HOLT</div><div class="stars">★★★★☆</div></div>
</section>

<!-- compare -->
<h2 class="abs h2" style="top:3410px">Compare Us</h2>
<div class="abs table">
  <div class="col labels"><div class="col-head">FEATURES</div><ul><li>Speed</li><li>Ease of Use</li><li>Cost</li><li>Availability</li><li>Pain</li></ul></div>
  <div class="col"><div class="col-head">GLOWBEAM</div><ul><li>1-2 Hours</li><li>Difficult / Dentist</li><li>$300 - $600</li><li>Limited Availability</li><li>Pain &amp; Sensitivity</li></ul></div>
  <div class="col"><div class="col-head brandhead"><i></i>Bright Harbor</div><ul><li>45 Mins</li><li>Very Easy</li><li>$378</li><li>Appt Only</li><li>No Pain</li></ul></div>
  <div class="col"><div class="col-head">SHINERIGHT</div><ul><li>7-14 Days</li><li>Difficult / Dentist</li><li>$300 - $600</li><li>Limited Availability</li><li>Sensitivity</li></ul></div>
  <div class="col"><div class="col-head">HOME KITS</div><ul><li>7-30 Days</li><li>Difficult</li><li>$50 - $150</li><li>Store Purchase</li><li>Sensitivity</li></ul></div>
</div>

<!-- footer -->
<footer class="abs footer">
  <div class="abs socials"><span>fk</span><span>ch</span><span>sl</span><span>PG</span></div>
  <p class="abs foot-line" style="top:162px">◷ Clinic Open: Mon-Fri 9:15 am to 5:30 pm Sat 10am to 2pm &nbsp;|&nbsp; Book Appointments: Mon-Fri 830 am to 5 pm</p>
  <p class="abs foot-line foot-links" style="top:204px">Home &nbsp;|&nbsp; Book Appointment Online &nbsp;|&nbsp; Our Process &nbsp;|&nbsp; Photos &nbsp;|&nbsp; Testimonials &nbsp;|&nbsp; Blog &nbsp;|&nbsp; FAQ &nbsp;|&nbsp; Contact &nbsp;|&nbsp; Gift Certificates &nbsp;|&nbsp; After Care<br>Consent Form Espanol &nbsp;|&nbsp; Consent Form English &nbsp;|&nbsp; Cancellation Policy &nbsp;|&nbsp; Privacy Policy &nbsp;|&nbsp; Free Treatments</p>
  <p class="abs foot-line" style="top:274px">Bright Harbor Smile Studio © 2018 All rights reserved.</p>
</footer>

</body>
</html>
```